Specialised investor in e-mobility and energy wants business card design

We need a business card design that fits our existing corporate design. <The look and feel must be 'sharp'/'clean', dynamic, communicate momentum, professionalism etc (as one would imagine from a firm in the financial sector). We like the idea of a reverse-side of the card that includes the logo, and the name and contact details on the other. We expect the deliverable to be whatever format might be required to be able to get cards printed directly by a service such as kelmo press. Our website is www.zub.capital

```html
<!DOCTYPE html>
<html lang="en">
<head>
<meta charset="utf-8">
<title>ZUB Capital – Business Card</title>
<link href="https://fonts.googleapis.com/css2?family=Montserrat:wght@400;500;700&display=swap" rel="stylesheet">
<style>
  :root {
    --green-dark: #2d4c21;
    --green-deep: #264219;
    --green-light: #7fad45;
    --band-white: #f2f3f1;
    --band-edge: #c9ccc7;
    --text-white: #ffffff;
    --backdrop: #e4e6e2;
  }
  * { margin: 0; padding: 0; box-sizing: border-box; }
  html, body { width: 1200px; height: 900px; overflow: hidden; }
  body {
    background: var(--backdrop);
    font-family: "Montserrat", sans-serif;
    position: relative;
  }
  .card {
    position: absolute;
    top: 150px;
    width: 340px;
    height: 600px;
    overflow: hidden;
    box-shadow: 0 14px 30px rgba(0,0,0,0.25);
  }
  .card-front { left: 220px; background: var(--green-dark); }
  .card-back {
    left: 640px;
    background: linear-gradient(160deg, var(--green-deep) 0%, var(--green-dark) 60%, #325426 100%);
  }
  .front-shapes { position: absolute; inset: 0; }

  .holder { position: absolute; top: 34px; right: 30px; text-align: right; }
  .holder-name {
    color: var(--green-light);
    font-weight: 700;
    font-size: 19px;
    letter-spacing: 0.2px;
  }
  .holder-role { color: var(--text-white); font-size: 14px; margin-top: 2px; }

  .wordmark {
    position: absolute;
    font-weight: 500;
    letter-spacing: -0.5px;
    white-space: nowrap;
  }
  .wordmark-front {
    top: 212px; left: 0; width: 340px; text-align: center;
    color: var(--green-dark); font-size: 42px;
  }
  .wordmark-back {
    bottom: 80px; right: 30px;
    color: var(--text-white); font-size: 36px;
  }

  .contact { position: absolute; left: 34px; right: 30px; bottom: 34px; color: var(--text-white); }
  .contact-row { display: flex; align-items: center; gap: 12px; font-size: 14.5px; height: 27px; }
  .contact-row svg { width: 16px; height: 16px; flex: none; }
  .contact-rule { height: 1px; background: var(--green-light); opacity: 0.8; margin: 10px 0; }
  .contact-rule.top { margin-top: 0; margin-bottom: 8px; }

  .web-vertical {
    position: absolute;
    top: 40px; left: 36px;
    writing-mode: vertical-rl;
    color: var(--text-white);
    font-size: 13px;
    letter-spacing: 7px;
  }
</style>
</head>
<body>

<section class="card card-front">
  <svg class="front-shapes" viewBox="0 0 340 600" aria-hidden="true">
    <rect width="340" height="600" fill="var(--green-dark)"/>
    <rect y="100" width="340" height="380" fill="var(--green-light)"/>
    <path d="M0,0 H340 V145 Q160,170 0,108 Z" fill="var(--green-dark)"/>
    <path d="M0,200 L85,158 Q210,150 340,150 V268 L262,328 Q130,326 0,340 Z" fill="var(--band-edge)"/>
    <path d="M0,196 L82,154 Q210,146 340,146 V264 L258,324 Q130,322 0,336 Z" fill="var(--band-white)"/>
    <path d="M0,340 Q190,312 340,478 V600 H0 Z" fill="var(--green-dark)"/>
  </svg>

  <div class="holder">
    <div class="holder-name">MARC VELLING</div>
    <div class="holder-role">Partner</div>
  </div>

  <div class="wordmark wordmark-front">ZUB Capital</div>

  <div class="contact">
    <div class="contact-row">
      <svg viewBox="0 0 16 16"><rect x="4" y="1" width="8" height="14" rx="1.5" fill="none" stroke="var(--green-light)" stroke-width="1.4"/><line x1="7" y1="12.5" x2="9" y2="12.5" stroke="var(--green-light)" stroke-width="1.4"/></svg>
      <span>+41 79555 0142</span>
    </div>
    <div class="contact-row">
      <svg viewBox="0 0 16 16"><rect x="1" y="3.5" width="14" height="9.5" rx="1" fill="none" stroke="var(--green-light)" stroke-width="1.4"/><path d="M1.5,4 L8,9 L14.5,4" fill="none" stroke="var(--green-light)" stroke-width="1.4"/></svg>
      <span>marc@zub.capital</span>
    </div>
    <div class="contact-rule top"></div>
    <div class="contact-row">
      <svg viewBox="0 0 16 16"><circle cx="8" cy="8" r="6.5" fill="none" stroke="var(--green-light)" stroke-width="1.4"/><ellipse cx="8" cy="8" rx="2.8" ry="6.5" fill="none" stroke="var(--green-light)" stroke-width="1.1"/><line x1="1.5" y1="8" x2="14.5" y2="8" stroke="var(--green-light)" stroke-width="1.1"/></svg>
      <span>www.zub.capital</span>
    </div>
    <div class="contact-rule"></div>
    <div class="contact-row">
      <svg viewBox="0 0 16 16"><path d="M8,15 C8,15 2.5,9 2.5,6 A5.5,5.5 0 0 1 13.5,6 C13.5,9 8,15 8,15 Z" fill="var(--green-light)"/><circle cx="8" cy="6" r="2" fill="var(--green-dark)"/></svg>
      <span>Lausanne, Switzerland</span>
    </div>
  </div>
</section>

<section class="card card-back">
  <div class="web-vertical">www.zub.capital</div>
  <div class="wordmark wordmark-back">ZUB Capital</div>
</section>

</body>
</html>
```